Lumbrix Design

Looking for Lumbrix banner and square design:
Lumbrix Banner
W:1600 px H:400 px
Square
120x120

Logo attached.

Description: Data-Driven stock market portfolio management using quantitative analysis.

```html
<!DOCTYPE html>
<html lang="en">
<head>
<meta charset="utf-8">
<title>Lumbrix Banner and Square</title>
<link href="https://fonts.googleapis.com/css2?family=Montserrat:wght@700&family=Roboto+Condensed:wght@700&family=Roboto:wght@400&display=swap" rel="stylesheet">
<style>
  :root {
    --stage-blue: #0b72b9;
    --brand-blue: #1a74b8;
    --navy: #1b5d8a;
    --deep-navy: #175c8c;
    --bright-blue: #1379c4;
    --banner-light: #f1f2f3;
    --banner-mid: #d9dbde;
    --banner-dark: #c3c6ca;
    --ink: #3b3b3b;
    --white: #ffffff;
  }
  * { margin: 0; padding: 0; box-sizing: border-box; }
  html, body {
    width: 1200px;
    height: 568px;
    overflow: hidden;
    background: var(--stage-blue);
  }
  .canvas {
    position: relative;
    width: 1200px;
    height: 568px;
  }
  .banner {
    position: absolute;
    left: 62px;
    top: 128px;
    width: 1076px;
    height: 269px;
    overflow: hidden;
    background: radial-gradient(ellipse at 48% 45%, var(--banner-light) 0%, var(--banner-mid) 60%, var(--banner-dark) 100%);
  }
  .growth-visual {
    position: absolute;
    left: 0;
    top: 0;
    width: 280px;
    height: 269px;
    background: linear-gradient(135deg, #c9ccd0 0%, #6f9cc2 45%, #1f6aa5 75%, #d9dbde 100%);
    opacity: 0.85;
  }
  .brand {
    position: absolute;
    left: 425px;
    top: 60px;
    display: flex;
    align-items: center;
    gap: 12px;
  }
  .brand-dot {
    width: 40px;
    height: 40px;
    border-radius: 50%;
    background: var(--brand-blue);
  }
  .brand-name {
    font-family: "Montserrat", sans-serif;
    font-weight: 700;
    font-size: 40px;
    line-height: 1;
    color: var(--brand-blue);
  }
  .headline {
    position: absolute;
    left: 305px;
    top: 132px;
    display: flex;
    align-items: center;
    gap: 8px;
    white-space: nowrap;
  }
  .headline-pill {
    background: var(--bright-blue);
    color: var(--white);
    font-family: "Roboto Condensed", sans-serif;
    font-weight: 700;
    font-size: 31px;
    line-height: 36px;
    padding: 0 7px;
    border-radius: 9px;
  }
  .headline-rest {
    font-family: "Montserrat", sans-serif;
    font-weight: 700;
    font-size: 31.5px;
    line-height: 36px;
    color: var(--navy);
  }
  .tagline {
    position: absolute;
    left: 305px;
    top: 173px;
    font-family: "Roboto", sans-serif;
    font-weight: 400;
    font-size: 20.5px;
    color: var(--ink);
    white-space: nowrap;
  }
  .device-showcase {
    position: absolute;
    left: 808px;
    top: 27px;
    width: 244px;
    height: 214px;
    border-radius: 8px;
    background: linear-gradient(160deg, #2a2d33 0%, #eef3f8 35%, #cfe1ef 70%, #b9bdc2 100%);
  }
  .square-mark {
    position: absolute;
    left: 558px;
    top: 355px;
    width: 85px;
    height: 85px;
    background: var(--deep-navy);
    border: 3px solid var(--white);
    display: flex;
    align-items: center;
    justify-content: center;
  }
  .square-name {
    font-family: "Montserrat", sans-serif;
    font-weight: 700;
    font-size: 15px;
    color: var(--white);
  }
</style>
</head>
<body>
<main class="canvas">
  <section class="banner">
    <div class="growth-visual" role="img" aria-label="Rising blue arrows over a faint grid, suggesting market growth"></div>

    <div class="brand">
      <span class="brand-dot"></span>
      <span class="brand-name">Lumbrix</span>
    </div>

    <h1 class="headline">
      <span class="headline-pill">DATA-DRIVEN</span>
      <span class="headline-rest">STOCK MARKET</span>
    </h1>
    <p class="tagline">Portfolio Management Using Quantitative Analysis.</p>

    <div class="device-showcase" role="img" aria-label="Desktop monitor and phone showing the portfolio dashboard with return charts"></div>
  </section>

  <div class="square-mark">
    <span class="square-name">Lumbrix</span>
  </div>
</main>
</body>
</html>
```